Machining Business Order Thank You Insert

I am looking for a business style card to include with orders that I ship. The card needs to thank the recipient for their order, and encourage them to leave a review. The card should include my business name and contact information and have an area to hand write a message.

I mainly sale on Craftlane and my own website. We are a machining an manufacturing business that are in the sale of mostly metal machined and 3d printed plastic products.

The front of the card should include the following:
Logo: (attached)
Snapgram: https://www.snapgram.example/kelvomill/
Friendsbook: https://www.friendsbook.example/KelvoMill
Website: https://www.kelvomill.example/

The back of the card needs an area to write a message

Industry/Entity Type

3D Printing, Machining, Craftlane

Contact Information for Business Card

Black or white front, white back to write a personal message

Font styles to use
Sans Serif

Colors

Designer to choose colors to be used in the design.

Requirements
Must have
• Encourage a review, social media info

```html
<!DOCTYPE html>
<html lang="en">
<head>
<meta charset="utf-8">
<title>KelvoMill – Order Thank You Card</title>
<link rel="stylesheet" href="https://fonts.googleapis.com/css2?family=Arimo:wght@400;700&family=Rajdhani:wght@600&display=swap">
<style>
  :root {
    --backdrop: #e4e4e2;
    --card-dark: #2d2d2f;
    --card-light: #ffffff;
    --card-edge: #d2461c;
    --accent: #e8501f;
    --ink-light: #f2f2f2;
    --ink-dark: #2d2d2f;
    --ink-muted: #6b6b6e;
    --rule: #8a8a8c;
    --write-line: #c9c9cc;
  }
  * { margin: 0; padding: 0; box-sizing: border-box; }
  html, body {
    width: 1200px; height: 801px; overflow: hidden;
    background: var(--backdrop);
    font-family: "Arimo", Arial, sans-serif;
  }
  .sheet { position: relative; width: 1200px; height: 801px; }
  .card {
    position: absolute; top: 245px;
    width: 540px; height: 310px;
    border-bottom: 4px solid var(--card-edge);
    border-left: 2px solid var(--card-edge);
    box-shadow: 0 10px 24px rgba(0,0,0,.18);
    overflow: hidden;
  }
  .card--front { left: 40px; background: var(--card-dark); }
  .card--back { left: 620px; background: var(--card-light); }

  .wordmark {
    font-family: "Rajdhani", "Arimo", sans-serif;
    font-weight: 600;
    letter-spacing: 0.42em;
    line-height: 1;
    white-space: nowrap;
  }

  /* Front */
  .brand-block { position: absolute; right: 40px; top: 30px; text-align: right; }
  .brand-block .mark-square {
    display: block; width: 56px; height: 56px;
    margin: 0 0 16px auto;
    background: var(--accent);
  }
  .card--front .wordmark { display: block; color: var(--ink-light); font-size: 24px; margin-right: -0.42em; }

  .divider {
    position: absolute; left: 200px; right: 40px; top: 150px;
    height: 1px; background: var(--rule);
  }
  .address {
    position: absolute; right: 40px; top: 166px;
    text-align: right; color: var(--ink-light);
    font-size: 14px; line-height: 1.3;
  }

  .contact-block { position: absolute; left: 36px; bottom: 26px; color: var(--ink-light); }
  .person-name { color: var(--accent); font-weight: 700; font-size: 21px; line-height: 1.1; }
  .person-role { font-size: 15px; margin-top: 2px; }
  .short-rule { width: 92px; height: 1px; background: var(--rule); margin: 8px 0 9px; }
  .contact-list { list-style: none; font-size: 14px; line-height: 1.55; }
  .contact-list li { display: flex; align-items: center; gap: 8px; }
  .contact-list svg { width: 13px; height: 13px; flex: none; }

  /* Back */
  .thanks-title {
    position: absolute; left: 36px; top: 28px;
    color: var(--accent); font-weight: 700; font-size: 21px; line-height: 1.1;
  }
  .review-prompt {
    position: absolute; left: 36px; top: 56px; right: 36px;
    color: var(--ink-muted); font-size: 13px; line-height: 1.35;
  }
  .message-area {
    position: absolute; left: 36px; right: 36px; top: 104px;
    list-style: none;
  }
  .message-area li { height: 32px; border-bottom: 1px solid var(--write-line); }
  .card--back .wordmark {
    position: absolute; right: 36px; bottom: 24px;
    color: var(--ink-dark); font-size: 20px; margin-right: -0.42em;
  }
</style>
</head>
<body>
<main class="sheet">
  <section class="card card--front" aria-label="Card front">
    <div class="brand-block">
      <span class="mark-square" aria-hidden="true"></span>
      <span class="wordmark">KELVOMILL</span>
    </div>
    <div class="divider"></div>
    <p class="address">Your address, city<br>state, ZIP 0000</p>

    <div class="contact-block">
      <p class="person-name">Marcus Hale</p>
      <p class="person-role">Manager</p>
      <div class="short-rule"></div>
      <ul class="contact-list">
        <li><svg viewBox="0 0 13 13" aria-hidden="true"><circle cx="6.5" cy="6.5" r="6.5" fill="var(--accent)"/></svg>kelvomill</li>
        <li><svg viewBox="0 0 13 13" aria-hidden="true"><circle cx="6.5" cy="6.5" r="6.5" fill="var(--accent)"/></svg>KelvoMill</li>
        <li><svg viewBox="0 0 13 13" aria-hidden="true"><circle cx="6.5" cy="6.5" r="6.5" fill="var(--accent)"/><circle cx="6.5" cy="6.5" r="3.6" fill="none" stroke="var(--card-dark)" stroke-width="1.1"/><path d="M2.9 6.5h7.2M6.5 2.9v7.2" stroke="var(--card-dark)" stroke-width="1.1"/></svg>www.kelvomill.example</li>
      </ul>
    </div>
  </section>

  <section class="card card--back" aria-label="Card back">
    <h2 class="thanks-title">Thank you for your order!</h2>
    <p class="review-prompt">Enjoying your part? Please leave us a review on Craftlane or at www.kelvomill.example</p>
    <ul class="message-area" aria-label="Space for a handwritten message">
      <li></li><li></li><li></li><li></li>
    </ul>
    <span class="wordmark">KELVOMILL</span>
  </section>
</main>
</body>
</html>
```